Laser Tattoo Removal Business Cards

We are looking for a professional business card design for a laser tattoo removal business. Ideally looking for a black business card design. The name of the business is Brightline Tattoo Removal. We place our cards at local tattoo shops so we ideally are looking for something trendy/edgy to draw both male and female clientele in.

Target Market(s)

Male/Female ages 18-60

Contact Information for Business Card

black background ideally.. hoping to stay within greys, whites and black

Font styles to use
Serif
Sans Serif

Colors
121212
a9a9a9
5c5c5c
f5f5f5
ffffff
7f7f7f
606060
848484
9d9d9d

Requirements
Must have
• Employee Info:
• Melissa Thornbury
• Chief Executive Offer
• m: 919.537.2846
• w: 919.362.4178
• f: 919.685.3907
• mthornbury@brightlinetattooremoval.example
• Address:
• 4615 Oakmere Pkwy, Suite 210
• Raleigh, NC 27654
• Website:
• www.brightlinetattooremoval.example
Nice to have
• Myabe business name on back or logo on back and employee info on the front

```html
<!DOCTYPE html>
<html lang="en">
<head>
<meta charset="utf-8">
<title>Brightline Tattoo Removal – Business Cards</title>
<link href="https://fonts.googleapis.com/css2?family=Arimo:wght@400;700&display=swap" rel="stylesheet">
<style>
  :root {
    --ink: #121212;
    --paper: #f5f5f5;
    --white: #ffffff;
    --grey-light: #a9a9a9;
    --grey-mid: #7f7f7f;
    --grey-dark: #5c5c5c;
    --stage: #e4e2de;
  }
  * { box-sizing: border-box; margin: 0; padding: 0; }
  html, body {
    width: 1200px;
    height: 886px;
    overflow: hidden;
    background: var(--stage);
    font-family: "Arimo", Arial, sans-serif;
  }
  .stage {
    position: relative;
    width: 1200px;
    height: 886px;
  }
  .card {
    position: absolute;
    top: 128px;
    width: 360px;
    height: 630px;
    display: flex;
    flex-direction: column;
    align-items: center;
    text-align: center;
    box-shadow: 0 6px 18px rgba(0,0,0,0.18);
  }
  .card--front { left: 200px; background: var(--paper); color: var(--ink); padding-top: 110px; }
  .card--back { left: 640px; background: var(--ink); color: var(--white); justify-content: center; }

  .brand {
    display: flex;
    flex-direction: column;
    align-items: center;
    gap: 10px;
    font-weight: 400;
    letter-spacing: 0.14em;
    text-transform: uppercase;
  }
  .brand__mark {
    width: 12px;
    height: 12px;
    background: currentColor;
  }
  .brand__name { font-size: 34px; line-height: 1; }
  .brand__sub { font-size: 17px; letter-spacing: 0.28em; }

  .contact { margin-top: 80px; line-height: 1.45; font-size: 15px; color: var(--grey-dark); }
  .contact__name {
    font-weight: 700;
    font-size: 20px;
    letter-spacing: 0.02em;
    text-transform: uppercase;
    color: var(--ink);
  }
  .contact__title { color: var(--grey-light); font-size: 15px; margin-bottom: 6px; }
  .contact__line { white-space: nowrap; }
  .contact__gap { margin-top: 10px; }
  .contact__small { font-size: 13.5px; }
</style>
</head>
<body>
<main class="stage">
  <section class="card card--front" aria-label="Business card front">
    <div class="brand">
      <span class="brand__mark" aria-hidden="true"></span>
      <span class="brand__name">Brightline</span>
      <span class="brand__sub">Tattoo Removal</span>
    </div>
    <div class="contact">
      <p class="contact__name">Melissa Thornbury</p>
      <p class="contact__title">Chief Executive Offer</p>
      <p class="contact__line">4615 Oakmere Pkwy, Suite 210</p>
      <p class="contact__line">Raleigh, NC 27654</p>
      <p class="contact__line contact__gap">P: 919.362.4178</p>
      <p class="contact__line">M: 919.537.2846 &nbsp;F: 919.685.3907</p>
      <p class="contact__line contact__small">mthornbury@brightlinetattooremoval.example</p>
      <p class="contact__line contact__small">www.brightlinetattooremoval.example</p>
    </div>
  </section>

  <section class="card card--back" aria-label="Business card back">
    <div class="brand">
      <span class="brand__mark" aria-hidden="true"></span>
      <span class="brand__name">Brightline</span>
      <span class="brand__sub">Tattoo Removal</span>
    </div>
  </section>
</main>
</body>
</html>
```